Lifecoach needs website design based on a standard Wordpress theme

I need a website for my new lifecoaching business that can be easily implemented in Wordpress, it needs to be compatible with a standard Wordpress theme. So I can place the pictures, texts etc. in a standard theme of Wordpress.

I want the design to be a very good feeling and playfull one, based on my logo.

Target Market(s)

I will coach people to reach their goals and dreams in life.

Industry/Entity Type

Business

Requirements
Must have
• Can be easy implemented in Wordpress.
Nice to have
• Photo's of nature are nice.

```html
<!DOCTYPE html>
<html lang="en">
<head>
<meta charset="utf-8">
<title>Ruben van Dalen – Lifecoach</title>
<link href="https://fonts.googleapis.com/css2?family=Noticia+Text:wght@400;700&family=Source+Sans+3:ital,wght@0,400;1,400&display=swap" rel="stylesheet">
<style>
:root{
  --blue:#1a8fd0;
  --text:#6e6e6e;
  --heading:#4a4a4a;
  --line:#e2e2e2;
  --nav-bg:#ececec;
  --footer:#3b3b3b;
  --footer-text:#d8d8d8;
}
*{margin:0;padding:0;box-sizing:border-box}
html,body{width:947px;height:1200px;overflow:hidden;background:#fff}
body{position:relative;font-family:"Source Sans 3",sans-serif;color:var(--text)}
.abs{position:absolute}

.site-header{left:0;top:0;width:947px;height:82px;background:linear-gradient(#fff,#f4f4f4)}
.brand{left:104px;top:16px;display:flex;align-items:center;gap:6px}
.brand-mark{width:48px;height:48px;border-radius:50%;border:3px solid var(--blue)}
.brand-name{font-family:"Noticia Text",serif;font-size:17px;color:var(--blue);line-height:1}

.main-nav{left:0;top:82px;width:947px;height:40px;background:linear-gradient(#f2f2f2,#e4e4e4);border-top:1px solid #ddd}
.main-nav a{position:absolute;top:0;height:40px;line-height:40px;font-family:"Noticia Text",serif;font-size:9.5px;color:#555;text-decoration:none;transform:translateX(-50%)}
.main-nav a.is-active{background:#f9f9f9;top:7px;height:29px;line-height:22px;width:68px;text-align:center}

.hero-band{left:0;top:122px;width:947px;height:406px;background:linear-gradient(#fff 0%,#f0f0f0 40%,#e2e2e2 100%)}
.hero-shadow{left:110px;top:522px;width:727px;height:16px;border-radius:50%;box-shadow:0 6px 8px rgba(0,0,0,.12)}
.hero-slide{left:93px;top:146px;width:762px;height:325px;border-radius:4px;overflow:hidden;
  background:linear-gradient(#7fa8c8 0%,#d8dcc8 30%,#c9d86a 52%,#8fbf24 68%,#6a9a18 100%)}
.hero-caption{left:127px;top:232px;width:404px;height:174px;background:rgba(255,255,255,.82);border-radius:2px;padding:16px 13px}
.hero-title{font-family:"Noticia Text",serif;font-variant:small-caps;color:var(--heading);font-size:22px;line-height:32px}
.hero-title .sm{font-size:12px;text-transform:uppercase}
.hero-title .hl{color:var(--blue);font-size:24px}
.hero-caption p{margin-top:12px;font-size:10px;line-height:16px;color:#666}
.slider-dots{left:443px;top:497px;display:flex;gap:7px;align-items:center}
.slider-dots span{width:10px;height:10px;border-radius:50%;background:#fafafa;box-shadow:inset 0 1px 2px rgba(0,0,0,.15)}
.slider-dots span.is-current{background:#c4c4c4;width:11px;height:11px}

.service-card{top:595px;width:238px;height:275px;border:1px solid var(--line);border-radius:3px;background:#fff;box-shadow:0 3px 4px rgba(0,0,0,.05)}
.service-card h2{height:37px;line-height:37px;padding-left:12px;font-family:"Noticia Text",serif;font-weight:400;font-size:15px;color:var(--heading);background:linear-gradient(#fff,#ececec);border-bottom:1px solid var(--line)}
.service-photo{margin:14px 0 0 9px;width:219px;height:125px}
.service-card p{margin:17px 11px 0 11px;font-size:10px;line-height:16px}
.read-more{font-style:italic;font-size:10px;color:var(--blue);text-decoration:none}
.service-card .read-more{position:absolute;left:12px;top:251px}

.about{left:103px;top:914px;width:480px}
.about h2{font-family:"Noticia Text",serif;font-weight:400;font-size:18px;color:var(--heading)}
.about p{font-size:10px;line-height:16px;margin-top:14px;padding-left:2px}
.about p+p{margin-top:16px}
.about .read-more{display:block;margin-top:7px}
.video{left:608px;top:914px;width:237px;height:153px;border:2px solid #d0d0d0;background:linear-gradient(135deg,#c8d2dc,#e8ecef 50%,#9fb0c0)}
.play{left:696px;top:969px}

.site-footer{left:0;top:1114px;width:947px;height:86px;background:var(--footer)}
.footer-nav{left:105px;top:1136px;font-family:"Noticia Text",serif;font-size:10.5px;color:var(--footer-text);word-spacing:1px}
.footer-nav .sep{color:#999;margin:0 8px}
.legal{left:105px;top:1162px;font-size:9px;color:var(--footer-text)}
.follow{left:751px;top:1134px;font-family:"Noticia Text",serif;font-size:10px;color:var(--footer-text)}
.social{left:751px;top:1158px;display:flex;gap:5px}
.social span{width:18px;height:18px;border-radius:50%;background:#a9a9a9}
</style>
</head>
<body>
<header class="abs site-header">
  <div class="abs brand"><span class="brand-mark"></span><span class="brand-name">Ruben van Dalen</span></div>
</header>
<nav class="abs main-nav">
  <a class="is-active" style="left:139px">HOME</a>
  <a style="left:222px">ABOUT US</a>
  <a style="left:321px">SERVICES</a>
  <a style="left:414px">GALLERY</a>
  <a style="left:498px">BLOG</a>
  <a style="left:593px">TESTIMONIALS</a>
  <a style="left:704px">CONTACT US</a>
</nav>

<section class="abs hero-band"></section>
<div class="abs hero-shadow"></div>
<div class="abs hero-slide" role="img" aria-label="Green rolling meadow with a dirt path under a bright cloudy sky"></div>
<div class="abs hero-caption">
  <div class="hero-title"><span class="sm">We specialize in</span> <span class="hl">Transition Life</span><br>Coaching <span class="sm">for personal and</span> Professional<br>Empowerment.</div>
  <p>Lorem ipsum dolor sit amet, consectetur adipisicing elit, sed do eiusmod tempor incididunt ut labore et dolore magna aliqua. Ut enim ad minim</p>
</div>
<div class="abs slider-dots"><span></span><span></span><span></span><span class="is-current"></span></div>

<article class="abs service-card" style="left:102px">
  <h2>Executive Coaching</h2>
  <div class="service-photo" role="img" aria-label="Business people in a coaching meeting around a laptop" style="background:linear-gradient(135deg,#f4f1ee,#c9b8a8 60%,#8a7a6c)"></div>
  <p>Lorem ipsum dolor sit amet, consectetur adipi­sicing elit, sed do eiusmod tempor incididunt ut labore et dolore magna aliqua.</p>
  <a class="read-more" href="#">Read More &gt;&gt;</a>
</article>
<article class="abs service-card" style="left:354px">
  <h2>Leadership Training</h2>
  <div class="service-photo" role="img" aria-label="Audience in a training session with one man raising his hand" style="background:linear-gradient(135deg,#dfe3e6,#8e9aa6 55%,#3c4652)"></div>
  <p>Lorem ipsum dolor sit amet, consectetur adipi­sicing elit, sed do eiusmod tempor incididunt ut labore et dolore magna aliqua.</p>
  <a class="read-more" href="#" style="top:254px;left:14px">Read More &gt;&gt;</a>
</article>
<article class="abs service-card" style="left:607px">
  <h2>Empowerment</h2>
  <div class="service-photo" role="img" aria-label="Woman in a red top sitting calmly on a sofa" style="background:linear-gradient(135deg,#eef0f1,#e5dcd8 55%,#c98a86)"></div>
  <p>Lorem ipsum dolor sit amet, consectetur adipi­sicing elit, sed do eiusmod tempor incididunt ut labore et dolore magna aliqua.</p>
  <a class="read-more" href="#" style="top:252px;left:14px">Read More &gt;&gt;</a>
</article>

<section class="abs about">
  <h2>About Us</h2>
  <p>Lorem ipsum dolor sit amet, consectetur adipisicing elit, sed do eiusmod tempor incididunt ut labore et dolore magna aliqua. Ut enim ad minim veniam, quis nostrud exercitation ullamco.</p>
  <p>Duis aute irure dolor in reprehenderit in voluptate velit esse cillum dolore eu fugiat nulla pariatur. Lorem ipsum dolor sit amet, consectetur adipisicing elit, sed do eiusmod tempor incididunt ut labore et dolore magna aliqua. Ut enim ad minim veniam, quis nostrud exercitation ullamco laboris.</p>
  <a class="read-more" href="#">Read More &gt;&gt;</a>
</section>
<div class="abs video" role="img" aria-label="Video still of a smiling businessman in an office"></div>
<svg class="abs play" width="60" height="60" viewBox="0 0 60 60" aria-hidden="true">
  <circle cx="30" cy="30" r="29" fill="#3a3a3a" fill-opacity=".85"/>
  <path d="M23 16 L44 30 L23 44 Z" fill="#fff"/>
</svg>

<footer class="abs site-footer"></footer>
<div class="abs footer-nav">Home<span class="sep">/</span>About us<span class="sep">/</span>Services<span class="sep">/</span>Gallery<span class="sep">/</span>Blog<span class="sep">/</span>Testimonials<span class="sep">/</span>Contact us</div>
<div class="abs legal">©2014 life coaching - Terms of Service - Privacy Policy</div>
<div class="abs follow">Follow Us :</div>
<div class="abs social"><span></span><span></span><span></span><span></span></div>
</body>
</html>
```